Website for an electrical contractor :)

We are after a web site which can show pictures of our jobs and our capability in a professional, creative and easily understood way.

----- Brightvale Electrical ------

We really want a visually good looking website with three sections

Section one:
'Completed projects'
We have a few pictures of jobs which we've completed and would like to show off with a brief description. (see uploads)

Section two:
'Our capabilities'
Just a list of what services we offer

Section three:
We would like a 'contact us' section which people can send us a short msg and upload a file for plans to be able to send to us. We would need their name, phone number and email details. We would also need a short privacy policy saying 'we do not disclose information to third parties'.
We also want to display our contact number and postal address

Good luck :)

Target Market(s)

Adults 25 years+
Business owners
Builders
Real estate agents

Industry/Entity Type

Electrical

Colors

Designer to choose colors to be used in the design.

Requirements
Must have
• Visually appealing
Easy to understand
In the 'Completed projects' section, must have a list for each project we do i can upload pictures for it.

```html
<!DOCTYPE html>
<html lang="en">
<head>
<meta charset="utf-8">
<title>Brightvale Electrical</title>
<link href="https://fonts.googleapis.com/css2?family=Raleway:wght@400;500;600&family=Open+Sans:wght@400;600;700&display=swap" rel="stylesheet">
<style>
:root{
  --red:#e32029;
  --dark:#222;
  --text:#444;
  --muted:#666;
  --band:#f0f0f0;
  --field:#f2f2f2;
}
*{box-sizing:border-box;margin:0;padding:0}
html,body{width:768px;height:1200px;overflow:hidden;background:#fff}
body{position:relative;font-family:"Open Sans",sans-serif;color:var(--text)}
.abs{position:absolute}
h2,h3,.brand,.welcome{font-family:"Raleway",sans-serif;font-weight:500}

.top{left:0;top:0;width:768px;height:58px;background:#ececec}
.brand{left:104px;top:13px;display:flex;align-items:center;gap:7px}
.brand-dot{width:12px;height:12px;border-radius:50%;background:var(--red)}
.brand-name{font-size:25px;color:var(--dark);line-height:1}
.brand-sub{font-family:"Open Sans",sans-serif;font-size:4px;color:var(--muted);margin-top:2px;text-align:right}
.phones{right:103px;top:13px;text-align:right}
.phones div{font-family:"Raleway",sans-serif;font-weight:600;font-size:11px;color:var(--dark);display:flex;align-items:center;justify-content:flex-end;gap:6px;margin-bottom:4px}
.ph-ico{width:11px;height:11px;border-radius:50%;background:var(--red);display:inline-flex;align-items:center;justify-content:center}

.nav{left:0;top:58px;width:768px;height:23px;border-bottom:1px solid var(--red)}
.nav-item{position:absolute;top:4px;height:16px;line-height:16px;font-size:6.5px;color:var(--text)}
.nav-item.active{background:var(--red);color:#fff;font-weight:600;width:47px;text-align:center}
.search{right:103px;top:3px;width:129px;height:16px;border:1px solid #ccc;font-size:5px;color:#999;padding:4px 8px}
.search span{position:absolute;right:-1px;top:-1px;width:19px;height:16px;background:var(--red);display:flex;align-items:center;justify-content:center}

.slider{left:103px;top:91px;width:562px;height:239px;background:#ddd;padding:5px;box-shadow:0 4px 6px rgba(0,0,0,.12)}
.slide-photo{width:100%;height:100%;background:linear-gradient(180deg,#4a3d30 0%,#8a7560 45%,#cfc6b8 100%)}
.caption{left:5px;bottom:5px;width:226px;height:76px;background:#fff;padding:10px 10px}
.welcome{font-size:15px;color:var(--dark)}
.welcome b{font-weight:500;color:var(--red);font-size:19px}
.caption .sub{font-family:"Raleway",sans-serif;font-size:8.5px;letter-spacing:1.6px;color:var(--dark)}
.caption p{font-size:5px;line-height:1.7;margin-top:6px;color:var(--muted)}
.arrows{right:8px;bottom:6px;font-size:7px;color:#aaa}
.arrows b{color:var(--red)}

.section-title{width:768px;text-align:center;font-size:15px;color:var(--red);font-weight:600}
.projects{left:103px;top:383px;width:562px;display:flex;justify-content:space-between}
.project{width:130px}
.project .photo{height:77px;background:linear-gradient(180deg,#8c8070,#d6d0c6)}
.project h3{font-size:8.4px;color:var(--dark);margin:10px 0 8px;font-weight:500}
.project.featured h3{color:var(--red)}
.project p{font-size:5px;line-height:1.75;color:var(--muted);height:27px}
.btn{display:inline-block;margin-top:6px;width:48px;height:19px;line-height:19px;text-align:center;font-size:5.5px;font-weight:700;color:#fff;background:var(--red)}
.project.featured .btn{background:#111}

.band{left:0;top:562px;width:768px;height:460px;background:var(--band)}
.cap-title{font-size:14px;color:var(--dark);text-align:center;width:768px}
.cap-photo{background:linear-gradient(180deg,#5b8fd0 0%,#9cc0e6 40%,#6b6e70 60%,#8d8f8a 100%)}
.cap-photo.ind{background:linear-gradient(180deg,#4f7fc4 0%,#a9c6ea 30%,#c9c6bd 35%,#b4b0a6 80%,#d8d0bc 100%)}
.cap-block h3{font-size:11.5px;color:var(--dark);margin-bottom:8px}
.cap-list{display:grid;grid-template-columns:130px 130px;column-gap:14px;list-style:none}
.cap-list.wide{column-gap:22px}
.cap-list li{font-size:5.6px;font-weight:600;color:#444;height:14.4px;line-height:8px;padding-left:8px;position:relative}
.cap-list li::before{content:"";position:absolute;left:0;top:2.5px;width:3px;height:3px;background:#333}
.cap-list li.hl{background:var(--red);color:#fff;height:9px;line-height:9px;margin-bottom:5.4px;padding-left:12px}
.cap-list li.hl::before{background:#fff;left:4px;top:3px}

.foot h2{font-size:14px;color:var(--red);font-weight:600}
.info{list-style:none;font-size:5.5px;line-height:9.5px;margin-top:6px}
.info li{display:flex;gap:6px}
.info li i{width:5px;height:5px;margin-top:2px;background:#333;border-radius:1px;flex:none}
.info li i.pin{border-radius:50% 50% 50% 0}
.social{display:flex;gap:6px;margin-top:9px}
.social span{width:14px;height:14px;border-radius:50%;background:#888}
.social span:first-child{background:#3b5998}
.field{position:absolute;background:var(--field);font-size:5.5px;color:#888;padding:4px 5px;height:14px}
.submit{background:var(--red);color:#fff;font-family:"Open Sans",sans-serif;font-weight:700;font-size:9px;text-align:center;line-height:23px}
.copy{left:105px;top:1183px;font-size:5px;color:#444}
</style>
</head>
<body>

<header class="abs top">
  <div class="abs brand">
    <span class="brand-dot"></span>
    <div>
      <div class="brand-name">Brightvale</div>
      <div class="brand-sub">Electrical &amp; Communications &nbsp; EC0000</div>
    </div>
  </div>
  <div class="abs phones">
    <div><span class="ph-ico"><svg width="6" height="6" viewBox="0 0 10 10"><path d="M2 1l2 2-1 1.5a6 6 0 0 0 2.5 2.5L7 6l2 2-1.5 1.5C4 9 1 6 .5 2z" fill="#fff"/></svg></span>04 5550 1234</div>
    <div><span class="ph-ico"><svg width="6" height="6" viewBox="0 0 10 10"><rect x="1" y="4" width="8" height="5" fill="#fff"/><rect x="3" y="1" width="4" height="3" fill="#fff"/></svg></span>08 5550 6789</div>
  </div>
</header>

<nav class="abs nav">
  <span class="nav-item active" style="left:104px">Home</span>
  <span class="nav-item" style="left:173px">About Us</span>
  <span class="nav-item" style="left:237px">Our Projects</span>
  <span class="nav-item" style="left:310px">Our Capabilities</span>
  <span class="nav-item" style="left:395px">Blog</span>
  <span class="nav-item" style="left:444px">Contact Us</span>
  <div class="abs search">Search here...
    <span><svg width="7" height="7" viewBox="0 0 10 10"><circle cx="4" cy="4" r="3" fill="none" stroke="#fff" stroke-width="1.5"/><path d="M6.2 6.2L9 9" stroke="#fff" stroke-width="1.5"/></svg></span>
  </div>
</nav>

<section class="abs slider">
  <div class="slide-photo" role="img" aria-label="Photo of a finished commercial kitchenette with a glass-door fridge and benchtop"></div>
  <div class="abs caption">
    <div class="welcome">Welcome to <b>Brightvale</b></div>
    <div class="sub">Electrical &amp; Communications</div>
    <p>Lorem Ipsum is simply dummy text of the printing and typesetting industry. Lorem Ipsum has been</p>
    <div class="abs arrows">‹ <b>›</b></div>
  </div>
</section>

<h2 class="abs section-title" style="top:346px">Our Projects</h2>
<section class="abs projects">
  <article class="project featured">
    <div class="photo" role="img" aria-label="Project photo: fitted kitchenette with fridge"></div>
    <h3>Lorem Ipsum is simply dummy</h3>
    <p>Lorem Ipsum is simply dummy text of the printing and typesetting industry. Lorem Ipsum has been the industry</p>
    <span class="btn">Read More</span>
  </article>
  <article class="project">
    <div class="photo" role="img" aria-label="Project photo: large function hall with lighting"></div>
    <h3>Lorem Ipsum is simply dummy</h3>
    <p>Lorem Ipsum is simply dummy text of the printing and typesetting industry. Lorem Ipsum has been the industry</p>
    <span class="btn">Read More</span>
  </article>
  <article class="project">
    <div class="photo" role="img" aria-label="Project photo: lounge room with seating"></div>
    <h3>Lorem Ipsum is simply dummy</h3>
    <p>Lorem Ipsum is simply dummy text of the printing and typesetting industry. Lorem Ipsum has been the industry</p>
    <span class="btn">Read More</span>
  </article>
  <article class="project">
    <div class="photo" style="background:linear-gradient(180deg,#3a3d44,#8a8c86 60%,#6f6a55)" role="img" aria-label="Project photo: warehouse under construction"></div>
    <h3>Lorem Ipsum is simply dummy</h3>
    <p>Lorem Ipsum is simply dummy text of the printing and typesetting industry. Lorem Ipsum has been the industry</p>
    <span class="btn">Read More</span>
  </article>
</section>

<section class="abs band">
  <h2 class="abs cap-title" style="top:20px">Our Capabilities</h2>
  <div class="abs cap-photo" style="left:103px;top:54px;width:273px;height:172px" role="img" aria-label="Photo of new residential townhouses with paved driveway"></div>
  <div class="abs cap-block" style="left:391px;top:52px">
    <h3>Residential Capability Statement</h3>
    <ul class="cap-list wide">
      <li class="hl">24hr Support / faults</li><li>Ceiling fans</li>
      <li>Mains/sub mains cabling</li><li>Exhaust fans</li>
      <li>RCD (Safety Switch) installations</li><li>Kitchen / Bathroom Projects</li>
      <li>Smoke alarms</li><li>Re-wires</li>
      <li>Power points</li><li>Smart wiring</li>
      <li>Lighting points</li><li>Phone points</li>
      <li>External lighting</li><li>Data points</li>
      <li>Sensor lighting</li><li>Switchboard installations/relocations</li>
      <li>Switching</li><li>Compliance investigations/inspections</li>
      <li>Antennas and Arial points</li><li>Concrete and wall chasing</li>
      <li>Dimmers</li><li>Temporary builders site power</li>
    </ul>
  </div>
  <div class="abs cap-block" style="left:103px;top:266px">
    <h3>Commercial / Industrial Capability Statement</h3>
    <ul class="cap-list">
      <li class="hl">24hr Support / faults</li><li>Phone/data points</li>
      <li>Lighting/power design and consultation</li><li>Data cabinets</li>
      <li>Emergency and exit lighting</li><li>Data Networking</li>
      <li>Led strip lighting</li><li>IDF installations/relocations</li>
      <li>Energy efficient lighting</li><li>All power requirements</li>
      <li>Temporary lighting</li><li>All three phase power requirements</li>
      <li>Illuminated signage</li><li>Electrical rip outs / Disconnections</li>
      <li>Switchboard relocations</li><li>Thermal Imaging scans</li>
      <li>Maintenance</li><li>Commercial lighting</li>
      <li>RCD installation</li><li>Concrete and wall chasing</li>
    </ul>
  </div>
  <div class="abs cap-photo ind" style="left:391px;top:268px;width:274px;height:172px" role="img" aria-label="Photo of a concrete industrial building under construction"></div>
</section>

<footer>
  <div class="abs foot" style="left:103px;top:1037px">
    <h2>Contact Info</h2>
    <ul class="info">
      <li><i></i>04 5550 1234</li>
      <li><i></i>08 5550 6789</li>
      <li><i></i>hello@brightvale-example.com</li>
      <li><i class="pin"></i>P.O Box 410 Harbour Point W.A<br>6099 A.B.N: 00 000 000 000</li>
    </ul>
  </div>
  <div class="abs foot" style="left:247px;top:1037px">
    <h2>Follow Us On</h2>
    <div class="social"><span></span><span></span><span></span></div>
  </div>
  <div class="abs foot" style="left:391px;top:1037px;width:274px;height:140px">
    <h2>Contact From</h2>
    <div class="field" style="left:0;top:24px;width:130px">Enter Your Name :</div>
    <div class="field" style="left:144px;top:24px;width:130px">Enter Your Phone :</div>
    <div class="field" style="left:0;top:43px;width:274px">Enter Your Email :</div>
    <div class="field" style="left:0;top:62px;width:274px;height:48px">Massage :</div>
    <div class="abs submit" style="left:0;top:116px;width:274px;height:23px">Submit</div>
  </div>
  <div class="abs copy">All Copyrigts Reserved © Brightvale Electrical 2015. Privacy Policy</div>
</footer>

</body>
</html>
```